Working Capital graphics

Our business advisory firm requires 9 images to be re-created and improved in the branding of our business.

The 9 images have been uploaded below and the colours and branding of the business can be found at the website www.tallowmereadvisory.com.au

```html
<!DOCTYPE html>
<html lang="en">
<head>
<meta charset="utf-8">
<title>Working Capital Graphics — Tallowmere Advisory</title>
<link href="https://fonts.googleapis.com/css2?family=Jost:wght@500;600;700&display=swap" rel="stylesheet">
<style>
:root{
  --navy:#143a84;
  --ink:#0e1f4a;
  --royal:#1f4fb8;
  --sky:#0aaeef;
  --orange:#f7931e;
  --orange-soft:#fbb161;
  --peach:#fdc98e;
  --frame:#d3d3d3;
  --paper:#ffffff;
}
*{margin:0;padding:0;box-sizing:border-box}
html,body{width:1200px;height:1150px;overflow:hidden;background:var(--paper)}
body{font-family:"Jost",sans-serif}
.canvas{position:relative;width:1200px;height:1150px;background:var(--paper)}
.panel{position:absolute;border:2px solid var(--frame);background:var(--paper)}
.panel svg{display:block;width:100%;height:100%}
.defs{position:absolute;width:0;height:0}
svg text{font-family:"Jost",sans-serif}
.lbl{font-size:8.5px;font-weight:600;fill:var(--navy);text-anchor:middle}
.hub{font-size:17px;font-weight:600;fill:#fff;text-anchor:middle}
.tag{font-size:16px;font-weight:600;fill:#fff;text-anchor:middle;letter-spacing:.5px}
.tri{font-size:15px;font-weight:600;fill:#fff;text-anchor:middle}
.sat{font-size:9px;font-weight:600;fill:var(--navy);text-anchor:middle}
.wc{font-size:25px;font-weight:700;fill:#fff;text-anchor:middle}
.gear{font-size:15px;font-weight:600;fill:#fff;text-anchor:middle}
.chev{font-size:9px;font-weight:600;fill:#fff;text-anchor:middle}
.bub{font-size:9px;font-weight:600;fill:var(--navy);text-anchor:middle}
.leg{font-size:8px;font-weight:600;fill:var(--navy)}
.title{font-weight:700;fill:var(--navy)}
.head{font-size:8px;font-weight:600;fill:var(--navy);text-anchor:middle}
.pill{font-size:6.5px;font-weight:600;fill:#fff;text-anchor:middle}
.opill{font-size:8px;font-weight:500;fill:#fff;text-anchor:middle}
.num{font-weight:600;fill:var(--navy);text-anchor:middle}
.bar{font-size:12px;font-weight:600;fill:#fff;text-anchor:middle}
.axis{font-size:11px;font-weight:500;fill:var(--navy)}
.pt{font-size:11px;font-weight:600;fill:var(--orange)}
.ptl{font-size:9.5px;font-weight:600;fill:var(--navy)}
.seg{font-size:7.5px;font-weight:500;fill:#fff;text-anchor:middle}
.out{font-size:7.5px;font-weight:600;fill:var(--navy);text-anchor:middle}
.core{font-size:21px;font-weight:700;fill:var(--orange);text-anchor:middle}
.gears-art{position:absolute;inset:18px;border-radius:6px;background:linear-gradient(135deg,var(--ink) 0%,var(--royal) 50%,var(--sky) 100%)}
.brand{position:absolute;left:786px;top:985px;display:flex;align-items:center;gap:18px}
.brand-dot{width:82px;height:82px;border-radius:50%;background:var(--orange);flex:none}
.brand-name{font-family:"Jost",sans-serif;font-weight:700;font-size:41px;line-height:1;color:var(--sky)}
</style>
</head>
<body>
<div class="canvas">

<svg class="defs" aria-hidden="true">
  <defs>
    <marker id="tip-orange" viewBox="0 0 10 10" refX="8" refY="5" markerWidth="5" markerHeight="5" orient="auto"><path d="M0 0L10 5L0 10z" fill="#f7931e"/></marker>
    <marker id="tip-navy" viewBox="0 0 10 10" refX="8" refY="5" markerWidth="4" markerHeight="4" orient="auto"><path d="M0 0L10 5L0 10z" fill="#143a84"/></marker>
  </defs>
</svg>

<!-- Cycles: revenue, supply chain, expenditure -->
<section class="panel cycles" style="left:38px;top:29px;width:574px;height:559px">
<svg viewBox="62 47 938 913">
  <g class="cycle revenue">
    <circle cx="271" cy="253" r="76" fill="none" stroke="var(--navy)" stroke-width="3"/>
    <circle cx="271" cy="253" r="68" fill="var(--sky)"/>
    <text class="hub" x="271" y="248">REVENUE<tspan x="271" dy="19">MANAGEMENT</tspan></text>
    <text class="lbl" x="271" y="132">CUSTOMER<tspan x="271" dy="9">STRATEGY</tspan></text>
    <text class="lbl" x="339" y="148">SALES<tspan x="339" dy="9">MANAGEMENT</tspan></text>
    <text class="lbl" x="373" y="191">RISK<tspan x="373" dy="9">MANAGEMENT</tspan></text>
    <text class="lbl" x="388" y="244">CONTRACT<tspan x="388" dy="9">MANAGEMENT</tspan></text>
    <text class="lbl" x="378" y="302">SALES ORDER<tspan x="378" dy="9">PROCESSING</tspan></text>
    <text class="lbl" x="339" y="350">CREDIT<tspan x="339" dy="9">CHECK</tspan></text>
    <text class="lbl" x="276" y="368">ORDER<tspan x="276" dy="9">FULFILLMENT</tspan></text>
    <text class="lbl" x="212" y="357">BILLING</text>
    <text class="lbl" x="169" y="310">CUSTOMER<tspan x="169" dy="9">SERVICE</tspan></text>
    <text class="lbl" x="153" y="250">CASH<tspan x="153" dy="9">COLLECTION</tspan></text>
    <text class="lbl" x="168" y="188">RECEIPT &amp;<tspan x="168" dy="9">ALLOCATION</tspan><tspan x="168" dy="9">OF CASH</tspan></text>
    <text class="lbl" x="211" y="148">CASH<tspan x="211" dy="9">MANAGEMENT</tspan></text>
    <g stroke="var(--orange)" stroke-width="1.6" marker-end="url(#tip-orange)">
      <line x1="231" y1="144" x2="247" y2="139"/><line x1="293" y1="142" x2="309" y2="147"/>
      <line x1="348" y1="167" x2="360" y2="177"/><line x1="380" y1="211" x2="384" y2="227"/>
      <line x1="386" y1="267" x2="383" y2="283"/><line x1="366" y1="322" x2="355" y2="334"/>
      <line x1="318" y1="363" x2="303" y2="369"/><line x1="247" y1="368" x2="232" y2="362"/>
      <line x1="194" y1="336" x2="185" y2="324"/><line x1="158" y1="286" x2="157" y2="270"/>
      <line x1="156" y1="233" x2="160" y2="216"/><line x1="185" y1="177" x2="195" y2="165"/>
    </g>
  </g>

  <g class="cycle supply">
    <circle cx="791" cy="255" r="76" fill="none" stroke="var(--navy)" stroke-width="3"/>
    <circle cx="791" cy="255" r="68" fill="var(--sky)"/>
    <text class="hub" x="791" y="250">SUPPLY CHAIN<tspan x="791" dy="19">MANAGEMENT</tspan></text>
    <text class="lbl" x="791" y="131">SUPPLY<tspan x="791" dy="10">CHAIN</tspan><tspan x="791" dy="10">STRATEGY</tspan></text>
    <text class="lbl" x="872" y="146">PRODUCT<tspan x="872" dy="10">RANGE</tspan><tspan x="872" dy="10">MANAGEMENT</tspan></text>
    <text class="lbl" x="908" y="215">FORECASTING</text>
    <text class="lbl" x="908" y="277">SALES ORDER<tspan x="908" dy="10">FORECASTING</tspan></text>
    <text class="lbl" x="878" y="340">PRODUCTION<tspan x="878" dy="10">SCHEDULING</tspan></text>
    <text class="lbl" x="795" y="368">RAW<tspan x="795" dy="10">MATERIAL</tspan><tspan x="795" dy="10">PLANNING</tspan></text>
    <text class="lbl" x="709" y="344">PRODUCTION<tspan x="709" dy="10">PLANNING</tspan></text>
    <text class="lbl" x="669" y="281">PRODUCTION</text>
    <text class="lbl" x="673" y="219">WAREHOUSING</text>
    <text class="lbl" x="713" y="167">DISTRIBUTION</text>
    <g stroke="var(--orange)" stroke-width="1.6" marker-end="url(#tip-orange)">
      <line x1="746" y1="147" x2="761" y2="140"/><line x1="820" y1="141" x2="835" y2="147"/>
      <line x1="896" y1="182" x2="903" y2="197"/><line x1="911" y1="235" x2="912" y2="251"/>
      <line x1="905" y1="305" x2="897" y2="318"/><line x1="849" y1="371" x2="834" y2="377"/>
      <line x1="757" y1="372" x2="741" y2="366"/><line x1="683" y1="319" x2="678" y2="304"/>
      <line x1="675" y1="256" x2="676" y2="239"/><line x1="689" y1="194" x2="702" y2="181"/>
    </g>
  </g>

  <g class="cycle expenditure">
    <circle cx="533" cy="697" r="76" fill="none" stroke="var(--navy)" stroke-width="3"/>
    <circle cx="533" cy="697" r="68" fill="var(--sky)"/>
    <text class="hub" x="533" y="692">EXPENDITURE<tspan x="533" dy="19">MANAGEMENT</tspan></text>
    <text class="lbl" x="533" y="568">PURCHASING<tspan x="533" dy="9">STRATEGY</tspan></text>
    <text class="lbl" x="609" y="599">BUDGETING &amp;<tspan x="609" dy="9">FORECASTING</tspan></text>
    <text class="lbl" x="650" y="653">ORIGINATING<tspan x="650" dy="9">REQUIREMENTS</tspan></text>
    <text class="lbl" x="651" y="721">SELECTING &amp;<tspan x="651" dy="9">NEGOTIATING</tspan></text>
    <text class="lbl" x="618" y="780">ORDERING &amp;<tspan x="618" dy="9">CONTRACTING</tspan></text>
    <text class="lbl" x="539" y="815">RECEIVING &amp;<tspan x="539" dy="9">EVALUATING</tspan></text>
    <text class="lbl" x="457" y="787">DISCREPANCY<tspan x="457" dy="9">MANAGEMENT</tspan></text>
    <text class="lbl" x="417" y="733">INVOICE<tspan x="417" dy="9">PROCESSING</tspan></text>
    <text class="lbl" x="415" y="657">PAYMENT<tspan x="415" dy="9">ISSUANCE</tspan></text>
    <text class="lbl" x="457" y="595">CASH<tspan x="457" dy="9">MANAGEMENT</tspan></text>
    <g stroke="var(--orange)" stroke-width="1.6" marker-end="url(#tip-orange)">
      <line x1="487" y1="587" x2="503" y2="580"/><line x1="565" y1="576" x2="580" y2="587"/>
      <line x1="623" y1="619" x2="634" y2="633"/><line x1="651" y1="684" x2="651" y2="701"/>
      <line x1="646" y1="751" x2="636" y2="763"/><line x1="586" y1="801" x2="572" y2="809"/>
      <line x1="500" y1="814" x2="486" y2="806"/><line x1="444" y1="773" x2="437" y2="759"/>
      <line x1="413" y1="703" x2="414" y2="687"/><line x1="429" y1="633" x2="436" y2="619"/>
    </g>
  </g>

  <g class="captions">
    <rect x="179" y="428" width="184" height="41" fill="var(--navy)"/>
    <text class="tag" x="271" y="454">CUSTOMER TO CASH</text>
    <rect x="700" y="428" width="233" height="41" fill="var(--navy)"/>
    <text class="tag" x="816" y="454">FORECAST TO FULFILLMENT</text>
    <rect x="444" y="874" width="184" height="40" fill="var(--navy)"/>
    <text class="tag" x="536" y="900">PURCHASE TO PAY</text>
  </g>

  <g class="triangle">
    <path d="M533 330L675 472H392Z" fill="var(--orange)"/>
    <path d="M533 330V412M533 412L392 472M533 412L675 472" stroke="#fff" stroke-width="2.5" fill="none"/>
    <text class="tri" x="502" y="399" transform="rotate(-45 502 399)">A/R</text>
    <text class="tri" x="580" y="400" transform="rotate(45 580 400)">INVENTORY</text>
    <text class="tri" x="533" y="454">A/P</text>
    <g stroke="var(--navy)" stroke-width="3.5" marker-end="url(#tip-navy)">
      <line x1="459" y1="386" x2="442" y2="368"/>
      <line x1="607" y1="384" x2="631" y2="367"/>
      <line x1="538" y1="485" x2="538" y2="513"/>
    </g>
  </g>
</svg>
</section>

<!-- Working capital hub -->
<section class="panel hub-map" style="left:629px;top:26px;width:287px;height:281px">
<svg viewBox="1028 43 469 459">
  <g stroke="var(--navy)" stroke-width="3">
    <line x1="1262" y1="279" x2="1262" y2="134"/><line x1="1262" y1="279" x2="1357" y2="168"/>
    <line x1="1262" y1="279" x2="1404" y2="251"/><line x1="1262" y1="279" x2="1389" y2="349"/>
    <line x1="1262" y1="279" x2="1312" y2="413"/><line x1="1262" y1="279" x2="1213" y2="413"/>
    <line x1="1262" y1="279" x2="1136" y2="349"/><line x1="1262" y1="279" x2="1120" y2="252"/>
    <line x1="1262" y1="279" x2="1168" y2="168"/>
  </g>
  <circle cx="1262" cy="279" r="85" fill="#fff" stroke="var(--navy)" stroke-width="3.5"/>
  <circle cx="1262" cy="279" r="74" fill="var(--sky)"/>
  <text class="wc" x="1262" y="277">WORKING<tspan x="1262" dy="24">CAPITAL</tspan></text>
  <g fill="#fff" stroke="var(--orange)" stroke-width="3">
    <circle cx="1262" cy="134" r="38"/><circle cx="1357" cy="168" r="38"/>
    <circle cx="1404" cy="251" r="38"/><circle cx="1389" cy="349" r="38"/>
    <circle cx="1312" cy="413" r="38"/><circle cx="1213" cy="413" r="38"/>
    <circle cx="1136" cy="349" r="38"/><circle cx="1120" cy="252" r="38"/>
    <circle cx="1168" cy="168" r="38"/>
  </g>
  <text class="sat" x="1262" y="127">SUPPLY<tspan x="1262" dy="10">CHAIN</tspan><tspan x="1262" dy="10">ISSUES</tspan></text>
  <text class="sat" x="1357" y="167">PROCESS<tspan x="1357" dy="10">ISSUES</tspan></text>
  <text class="sat" x="1404" y="250" style="font-size:7.5px">FORECASTING<tspan x="1404" dy="9">AND PLANNING</tspan></text>
  <text class="sat" x="1389" y="347">CUSTOMER<tspan x="1389" dy="10">MANAGEMENT</tspan></text>
  <text class="sat" x="1312" y="407">SKU<tspan x="1312" dy="10">COMPLEXITY</tspan></text>
  <text class="sat" x="1213" y="407">SUPPLIER<tspan x="1213" dy="10">MANAGEMENT</tspan></text>
  <text class="sat" x="1136" y="348">KPIS AND<tspan x="1136" dy="10">MEASURES</tspan></text>
  <text class="sat" x="1120" y="245">IT SYSTEMS<tspan x="1120" dy="10">AND</tspan><tspan x="1120" dy="10">INFORMATION</tspan></text>
  <text class="sat" x="1168" y="167">TERMS AND<tspan x="1168" dy="10">CONDITIONS</tspan></text>
</svg>
</section>

<!-- Gears illustration area -->
<section class="panel gears" style="left:935px;top:35px;width:233px;height:270px">
  <div class="gears-art" role="img" aria-label="Illustration: three interlocking gears labelled accounts receivable, inventory and accounts payable, circled by orange arrows"></div>
</section>

<!-- Value chain levers -->
<section class="panel value-chain" style="left:629px;top:323px;width:475px;height:258px">
<svg viewBox="1028 527 775 421">
  <g stroke="var(--navy)" stroke-width="1.5" fill="none">
    <path d="M1103 697V720M1254 623V720M1176 720V707H1333V697M1524 697V720M1647 623V720M1725 697V720"/>
    <path d="M1254 795V812M1647 795V812M1725 795V812"/>
    <path d="M1268 795V806H1571V795M1341 795V806M1420 795V806M1497 795V806"/>
  </g>
  <g class="chevrons">
    <path d="M1067 720H1143L1155 757L1143 795H1067Z" fill="var(--ink)"/>
    <path d="M1143 720H1218L1230 757L1218 795H1143L1155 757Z" fill="var(--navy)"/>
    <path d="M1218 720H1293L1305 757L1293 795H1218L1230 757Z" fill="var(--royal)"/>
    <path d="M1293 720H1376L1388 757L1376 795H1293L1305 757Z" fill="var(--sky)"/>
    <path d="M1376 720H1450L1462 757L1450 795H1376L1388 757Z" fill="var(--orange)"/>
    <path d="M1450 720H1526L1538 757L1526 795H1450L1462 757Z" fill="var(--orange-soft)"/>
    <path d="M1526 720H1602L1614 757L1602 795H1526L1538 757Z" fill="var(--peach)"/>
    <path d="M1602 720H1678L1690 757L1678 795H1602L1614 757Z" fill="var(--ink)"/>
    <path d="M1678 720H1753L1765 757L1753 795H1678L1690 757Z" fill="var(--navy)"/>
    <text class="chev" x="1110" y="761">DESIGN</text>
    <text class="chev" x="1186" y="749">ORDER/<tspan x="1186" dy="10">MATERIAL</tspan><tspan x="1186" dy="10">PLANNING</tspan></text>
    <text class="chev" x="1268" y="761">PURCHASING</text>
    <text class="chev" x="1346" y="761" style="font-size:8.5px">MANUFACTURING</text>
    <text class="chev" x="1426" y="761" style="font-size:8.5px">PRE-ASSEMBLY</text>
    <text class="chev" x="1499" y="761">ASSEMBLY</text>
    <text class="chev" x="1572" y="755">PACKAGING/<tspan x="1572" dy="10">SHIPPING</tspan></text>
    <text class="chev" x="1644" y="761">SALES</text>
    <text class="chev" x="1726" y="755">AFTER SALES/<tspan x="1726" dy="10">SERVICE</tspan></text>
  </g>
  <g class="levers" fill="#fff" stroke-width="2.5">
    <circle cx="1103" cy="663" r="34" stroke="var(--orange)"/>
    <circle cx="1254" cy="589" r="34" stroke="var(--sky)"/>
    <circle cx="1254" cy="663" r="34" stroke="var(--sky)"/>
    <circle cx="1333" cy="663" r="34" stroke="var(--sky)"/>
    <circle cx="1524" cy="663" r="34" stroke="var(--orange)"/>
    <circle cx="1647" cy="589" r="34" stroke="var(--sky)"/>
    <circle cx="1647" cy="663" r="34" stroke="var(--sky)"/>
    <circle cx="1725" cy="663" r="34" stroke="var(--sky)"/>
    <circle cx="1254" cy="846" r="34" stroke="var(--sky)"/>
    <circle cx="1647" cy="846" r="34" stroke="var(--orange)"/>
    <circle cx="1725" cy="846" r="34" stroke="var(--orange)"/>
  </g>
  <text class="bub" x="1103" y="656">REDUCE PART<tspan x="1103" dy="10">VARIANTS/</tspan><tspan x="1103" dy="10">RELEASES</tspan></text>
  <text class="bub" x="1254" y="582">MODIFY<tspan x="1254" dy="10">PAYMENT</tspan><tspan x="1254" dy="10">CONDITIONS</tspan></text>
  <text class="bub" x="1254" y="656">OPTIMIZE<tspan x="1254" dy="10">PAYMENT</tspan><tspan x="1254" dy="10">PROCESSES</tspan></text>
  <text class="bub" x="1333" y="647" style="font-size:7.5px">RETHINK<tspan x="1333" dy="8.5">DELIVERY</tspan><tspan x="1333" dy="8.5">SCHEDULES</tspan><tspan x="1333" dy="8.5">AND</tspan><tspan x="1333" dy="8.5">WAREHOUSING</tspan></text>
  <text class="bub" x="1524" y="656">OPTIMIZE<tspan x="1524" dy="10">PRODUCT</tspan><tspan x="1524" dy="10">TESTING</tspan></text>
  <text class="bub" x="1647" y="582">IMPROVE<tspan x="1647" dy="10">PAYMENT</tspan><tspan x="1647" dy="10">SCHEMES</tspan></text>
  <text class="bub" x="1647" y="656" style="font-size:8px">REDUCE DUE/<tspan x="1647" dy="10">OVERDUE</tspan><tspan x="1647" dy="10">RECEIVABLE</tspan></text>
  <text class="bub" x="1725" y="656" style="font-size:7.5px">ESTABLISH NEW<tspan x="1725" dy="10">PAYMENT</tspan><tspan x="1725" dy="10">CONDITIONS</tspan></text>
  <text class="bub" x="1254" y="839">OPTIMIZE<tspan x="1254" dy="10">EXTERNAL</tspan><tspan x="1254" dy="10">PURCHASING</tspan></text>
  <text class="bub" x="1647" y="833">REDUCE<tspan x="1647" dy="9.5">FINISHED</tspan><tspan x="1647" dy="9.5">GOODS</tspan><tspan x="1647" dy="9.5">STOCKS</tspan></text>
  <text class="bub" x="1725" y="843">REDUCE<tspan x="1725" dy="10">INVENTORY</tspan></text>
  <g class="legend">
    <circle cx="1470" cy="907" r="5" fill="none" stroke="var(--sky)" stroke-width="2"/>
    <path d="M1470 902A5 5 0 0 0 1470 912" fill="none" stroke="var(--orange)" stroke-width="2"/>
    <text class="leg" x="1480" y="910">INVENTORY</text>
    <circle cx="1545" cy="907" r="5" fill="none" stroke="var(--orange)" stroke-width="2"/>
    <text class="leg" x="1556" y="906">PAYABLES AND<tspan x="1556" dy="9">PRE-PAYMENTS MADE</tspan></text>
    <circle cx="1660" cy="907" r="5" fill="none" stroke="var(--sky)" stroke-width="2"/>
    <text class="leg" x="1672" y="906">RECEIVABLES AND<tspan x="1672" dy="9">PRE-PAYMENTS RECEIVED</tspan></text>
  </g>
</svg>
</section>

<!-- Receivables drivers -->
<section class="panel receivables" style="left:39px;top:603px;width:365px;height:219px">
<svg viewBox="63 985 596 358">
  <text class="title" x="95" y="1027" style="font-size:17px">RECEIVABLES</text>
  <text class="head" x="272" y="1023">SUB-PROCESS</text>
  <text class="head" x="407" y="1023">DRIVERS</text>
  <text class="head" x="561" y="1061">SUB-DRIVERS</text>
  <g stroke="var(--navy)" stroke-width="1.2" fill="none">
    <path d="M201 1158H228M228 1062V1252M228 1062H237M228 1152H237M228 1252H237"/>
    <path d="M320 1062H330M330 1040V1084M330 1040H342M330 1062H342M330 1084H342"/>
    <path d="M320 1152H330M330 1134V1178M330 1134H342M330 1156H342M330 1178H342"/>
    <path d="M320 1252H330M330 1239V1283M330 1239H342M330 1261H342M330 1283H342"/>
    <path d="M473 1134H487M487 1080V1139M487 1080H502M487 1097H502M487 1123H502M487 1139H502"/>
    <path d="M473 1156H487V1178M473 1178H502M487 1162H502M487 1195H502M487 1162V1195"/>
    <path d="M473 1239H487M487 1221V1254M487 1221H502M487 1237H502M487 1254H502"/>
    <path d="M473 1261H487M487 1277V1310M487 1261V1277M487 1277H502M487 1293H502M487 1310H502"/>
  </g>
  <circle cx="148" cy="1158" r="53" fill="#fff" stroke="var(--navy)" stroke-width="2"/>
  <circle cx="148" cy="1158" r="47" fill="var(--sky)"/>
  <text class="opill" x="148" y="1155" style="font-size:11px;font-weight:600">RECEIVABLES<tspan x="148" dy="12">DRIVERS</tspan></text>
  <g fill="var(--orange)">
    <rect x="237" y="1053" width="83" height="18" rx="9"/>
    <rect x="237" y="1143" width="83" height="18" rx="9"/>
    <rect x="237" y="1243" width="83" height="18" rx="9"/>
  </g>
  <text class="opill" x="278" y="1065">APPROVAL</text>
  <text class="opill" x="278" y="1155">SALES</text>
  <text class="opill" x="278" y="1255">COLLECTIONS</text>
  <g fill="var(--sky)">
    <rect x="362" y="1034" width="111" height="12" rx="6"/><rect x="362" y="1056" width="111" height="12" rx="6"/>
    <rect x="362" y="1078" width="111" height="12" rx="6"/><rect x="362" y="1128" width="111" height="12" rx="6"/>
    <rect x="362" y="1150" width="111" height="12" rx="6"/><rect x="362" y="1172" width="111" height="12" rx="6"/>
    <rect x="362" y="1233" width="111" height="12" rx="6"/><rect x="362" y="1255" width="111" height="12" rx="6"/>
    <rect x="362" y="1277" width="111" height="12" rx="6"/>
    <rect x="502" y="1075" width="124" height="11" rx="5.5"/><rect x="502" y="1092" width="124" height="11" rx="5.5"/>
    <rect x="502" y="1118" width="124" height="11" rx="5.5"/><rect x="502" y="1134" width="124" height="11" rx="5.5"/>
    <rect x="502" y="1157" width="124" height="11" rx="5.5"/><rect x="502" y="1173" width="124" height="11" rx="5.5"/>
    <rect x="502" y="1190" width="124" height="11" rx="5.5"/><rect x="502" y="1216" width="124" height="11" rx="5.5"/>
    <rect x="502" y="1232" width="124" height="11" rx="5.5"/><rect x="502" y="1249" width="124" height="11" rx="5.5"/>
    <rect x="502" y="1272" width="124" height="11" rx="5.5"/><rect x="502" y="1288" width="124" height="11" rx="5.5"/>
    <rect x="502" y="1305" width="124" height="11" rx="5.5"/>
  </g>
  <g fill="#fff" stroke="var(--orange)" stroke-width="1.5">
    <circle cx="350" cy="1040" r="8"/><circle cx="350" cy="1062" r="8"/><circle cx="350" cy="1084" r="8"/>
    <circle cx="350" cy="1134" r="8"/><circle cx="350" cy="1156" r="8"/><circle cx="350" cy="1178" r="8"/>
    <circle cx="350" cy="1239" r="8"/><circle cx="350" cy="1261" r="8"/><circle cx="350" cy="1283" r="8"/>
  </g>
  <g class="num" style="font-size:10px">
    <text x="350" y="1044">1</text><text x="350" y="1066">2</text><text x="350" y="1088">3</text>
    <text x="350" y="1138">4</text><text x="350" y="1160">5</text><text x="350" y="1182">6</text>
    <text x="350" y="1243">7</text><text x="350" y="1265">8</text><text x="350" y="1287">9</text>
  </g>
  <text class="pill" x="417" y="1043">DIFFERENTIATED TERMS</text>
  <text class="pill" x="417" y="1065">COSTUMER AGREEMENTS</text>
  <text class="pill" x="417" y="1087">ACCOUNT SET-UP</text>
  <text class="pill" x="417" y="1137">RECEIPT PROCESS</text>
  <text class="pill" x="417" y="1159">TIME TO INVOICE</text>
  <text class="pill" x="417" y="1181" style="font-size:5.8px">COSTUMER PAYMENT BEHAVIOUR</text>
  <text class="pill" x="417" y="1242">PAYMENT CYCLE</text>
  <text class="pill" x="417" y="1264">COLLECTIONS</text>
  <text class="pill" x="417" y="1286">PENALTIES</text>
  <text class="pill" x="564" y="1083">CASH</text>
  <text class="pill" x="564" y="1100">BANKING PROCESS</text>
  <text class="pill" x="564" y="1126">SALES DELIVERY</text>
  <text class="pill" x="564" y="1142">INVOICING</text>
  <text class="pill" x="564" y="1165">KPI</text>
  <text class="pill" x="564" y="1181">RELATIONSHIP</text>
  <text class="pill" x="564" y="1198">PRICING</text>
  <text class="pill" x="564" y="1224">CLOSING DATE</text>
  <text class="pill" x="564" y="1240">TIME TO PROCESS</text>
  <text class="pill" x="564" y="1257">INVOICING CYCLE</text>
  <text class="pill" x="564" y="1280">TRACKING</text>
  <text class="pill" x="564" y="1296">METHODS</text>
  <text class="pill" x="564" y="1313">AGENCIES</text>
</svg>
</section>

<!-- Payables drivers -->
<section class="panel payables" style="left:416px;top:603px;width:338px;height:218px">
<svg viewBox="680 985 551 356">
  <text class="title" x="719" y="1032" style="font-size:22px">PAYABLES</text>
  <text class="head" x="1035" y="1035" style="font-size:14px">DRIVERS</text>
  <path d="M836 1188H866M866 1081V1294M866 1081H878M866 1136H878M866 1187H878M866 1240H878M866 1294H878" stroke="var(--navy)" stroke-width="1.5" fill="none"/>
  <circle cx="778" cy="1188" r="58" fill="#fff" stroke="var(--navy)" stroke-width="2"/>
  <circle cx="778" cy="1188" r="51" fill="var(--sky)"/>
  <text class="gear" x="778" y="1186">PAYABLES<tspan x="778" dy="15">DRIVERS</tspan></text>
  <g fill="var(--sky)">
    <rect x="905" y="1067" width="287" height="28" rx="14"/><rect x="905" y="1122" width="287" height="28" rx="14"/>
    <rect x="905" y="1173" width="287" height="28" rx="14"/><rect x="905" y="1226" width="287" height="28" rx="14"/>
    <rect x="905" y="1280" width="287" height="28" rx="14"/>
  </g>
  <g fill="#fff" stroke="var(--orange)" stroke-width="2.5">
    <circle cx="893" cy="1081" r="17"/><circle cx="893" cy="1136" r="17"/><circle cx="893" cy="1187" r="17"/>
    <circle cx="893" cy="1240" r="17"/><circle cx="893" cy="1294" r="17"/>
  </g>
  <g class="num" style="font-size:19px">
    <text x="893" y="1088">14</text><text x="893" y="1143">15</text><text x="893" y="1194">16</text>
    <text x="893" y="1247">17</text><text x="893" y="1301">18</text>
  </g>
  <text class="bar" x="1039" y="1085">REDUCE EARLY PAYMENTS</text>
  <text class="bar" x="1039" y="1140">REDUCE OVER-RIDES</text>
  <text class="bar" x="1039" y="1191">REDUCE VENDOR CREDITS</text>
  <text class="bar" x="1043" y="1244">INCREASE PO VENDOR TERMS</text>
  <text class="bar" x="1043" y="1298">INCREASE INVOICE ONLY TERMS</text>
</svg>
</section>

<!-- Net working capital absorption -->
<section class="panel absorption" style="left:766px;top:603px;width:247px;height:218px">
<svg viewBox="1252 985 403 356">
  <text class="title" x="1296" y="1016" style="font-size:13.5px">NETWORKING CAPITAL ABSORPTION</text>
  <g class="axis" text-anchor="end">
    <text x="1324" y="1042">450m</text><text x="1324" y="1075">400m</text><text x="1324" y="1108">350m</text>
    <text x="1324" y="1141">300m</text><text x="1324" y="1174">250m</text><text x="1324" y="1207">200m</text>
    <text x="1324" y="1240">150m</text><text x="1324" y="1273">100m</text>
  </g>
  <g class="axis" text-anchor="middle">
    <text x="1357" y="1299">20m</text><text x="1397" y="1299">25m</text><text x="1436" y="1299">30m</text>
    <text x="1476" y="1299">35m</text><text x="1516" y="1299">40m</text><text x="1555" y="1299">45m</text>
  </g>
  <text class="title" x="1460" y="1323" text-anchor="middle" style="font-size:11.5px">NET WORKING CAPITAL (NWC)</text>
  <text class="pt" x="1287" y="1158" transform="rotate(-90 1287 1158)" text-anchor="middle" style="font-size:9px">SALES</text>
  <path d="M1337 1032V1283H1585" stroke="var(--navy)" stroke-width="1.5" fill="none"/>
  <path d="M1462 1155H1540A78 78 0 1 1 1462 1077Z" fill="var(--sky)"/>
  <g stroke="var(--navy)" stroke-width="1" stroke-dasharray="3 3">
    <line x1="1337" y1="1155" x2="1462" y2="1155"/><line x1="1462" y1="1155" x2="1462" y2="1283"/>
  </g>
  <g stroke="var(--navy)" stroke-width="1" marker-end="url(#tip-navy)">
    <line x1="1462" y1="1155" x2="1462" y2="1050"/><line x1="1462" y1="1155" x2="1517" y2="1076"/>
    <line x1="1462" y1="1155" x2="1559" y2="1155"/><line x1="1462" y1="1155" x2="1521" y2="1221"/>
    <line x1="1462" y1="1155" x2="1389" y2="1216"/><line x1="1462" y1="1155" x2="1400" y2="1089"/>
  </g>
  <circle cx="1462" cy="1155" r="5" fill="var(--navy)"/>
  <text class="pt" x="1459" y="1046">B</text>
  <text class="pt" x="1389" y="1083">A</text>
  <text class="ptl" x="1351" y="1066">OPTIMAL GROWTH</text>
  <text class="pt" x="1515" y="1068">C</text>
  <text class="ptl" x="1530" y="1068">FAST GROWTH</text>
  <text class="pt" x="1553" y="1147">D</text>
  <text class="ptl" x="1571" y="1141">DECLINING<tspan x="1571" dy="9">GROWTH</tspan></text>
  <text class="pt" x="1525" y="1225">E</text>
  <text class="ptl" x="1543" y="1226">CORPORATE STRESS</text>
  <text class="pt" x="1372" y="1224">F</text>
  <text class="ptl" x="1376" y="1243">DOWNSIZING</text>
</svg>
</section>

<!-- Inventory drivers -->
<section class="panel inventories" style="left:39px;top:845px;width:365px;height:269px">
<svg viewBox="63 1381 596 439">
  <text class="title" x="107" y="1441" style="font-size:18px">INVENTORIES</text>
  <text class="head" x="338" y="1443" style="font-size:11px">DRIVER GROUP</text>
  <text class="head" x="531" y="1443" style="font-size:11px">SUB-GROUP</text>
  <g stroke="var(--navy)" stroke-width="1.3" fill="none">
    <path d="M233 1624H260M260 1501V1742M260 1501H273M260 1589H273M260 1663H273M260 1742H273"/>
    <path d="M403 1501H433M433 1462V1538M433 1462H449M433 1488H449M433 1513H449M433 1538H449"/>
    <path d="M403 1589H433M433 1565V1615M433 1565H449M433 1590H449M433 1615H449"/>
    <path d="M403 1663H433M433 1641V1687M433 1641H449M433 1663H449M433 1687H449"/>
    <path d="M403 1742H433M433 1716V1768M433 1716H449M433 1742H449M433 1768H449"/>
  </g>
  <circle cx="170" cy="1624" r="63" fill="#fff" stroke="var(--navy)" stroke-width="2"/>
  <circle cx="170" cy="1624" r="56" fill="var(--sky)"/>
  <text class="gear" x="170" y="1621">INVENTORY<tspan x="170" dy="17">DRIVERS</tspan></text>
  <g fill="var(--sky)">
    <rect x="294" y="1490" width="110" height="22" rx="11"/><rect x="294" y="1578" width="110" height="22" rx="11"/>
    <rect x="294" y="1652" width="110" height="22" rx="11"/><rect x="294" y="1731" width="110" height="22" rx="11"/>
    <rect x="449" y="1455" width="165" height="14" rx="7"/><rect x="449" y="1481" width="165" height="14" rx="7"/>
    <rect x="449" y="1506" width="165" height="14" rx="7"/><rect x="449" y="1531" width="165" height="14" rx="7"/>
    <rect x="449" y="1558" width="165" height="14" rx="7"/><rect x="449" y="1583" width="165" height="14" rx="7"/>
    <rect x="449" y="1608" width="165" height="14" rx="7"/><rect x="449" y="1634" width="165" height="14" rx="7"/>
    <rect x="449" y="1656" width="165" height="14" rx="7"/><rect x="449" y="1680" width="165" height="14" rx="7"/>
    <rect x="449" y="1709" width="165" height="14" rx="7"/><rect x="449" y="1735" width="165" height="14" rx="7"/>
    <rect x="449" y="1761" width="165" height="14" rx="7"/>
  </g>
  <g fill="#fff" stroke="var(--orange)" stroke-width="2">
    <circle cx="286" cy="1501" r="13"/><circle cx="286" cy="1589" r="13"/>
    <circle cx="286" cy="1663" r="13"/><circle cx="286" cy="1742" r="13"/>
  </g>
  <g class="num" style="font-size:15px">
    <text x="286" y="1506">10</text><text x="286" y="1594">11</text><text x="286" y="1668">12</text><text x="286" y="1747">13</text>
  </g>
  <g class="opill" style="font-size:10px;text-anchor:start">
    <text x="315" y="1505">PLANNING</text><text x="315" y="1593">PROCUREMENT</text>
    <text x="315" y="1667">FULFILMENT</text><text x="315" y="1746">PRODUCT RANGE</text>
  </g>
  <text class="pill" x="531" y="1465">DEMAND VARIABILITY</text>
  <text class="pill" x="531" y="1491">PLANNING COLLABORATION</text>
  <text class="pill" x="531" y="1516">INFORMATION AVAILABILITY</text>
  <text class="pill" x="531" y="1541">INVENTROY TARGET SETTING</text>
  <text class="pill" x="531" y="1568">ORDER QUANTITIES</text>
  <text class="pill" x="531" y="1593">SUPPLIER LEAD TIME VARIABILITY</text>
  <text class="pill" x="531" y="1618">SUPPLIER QUALITY VARIABILITY</text>
  <text class="pill" x="531" y="1644">CUSTOMER SERVICE LEVELS</text>
  <text class="pill" x="531" y="1666">NETWORK STRUCTURE</text>
  <text class="pill" x="531" y="1690">INVENTORY POSTPONEMENT</text>
  <text class="pill" x="531" y="1719">CUSTOMER INVENTORY NEEDS</text>
  <text class="pill" x="531" y="1745">PART STANDARDISATION</text>
  <text class="pill" x="531" y="1771">SKU PROLIFERATION</text>
</svg>
</section>

<!-- Next $100 of sales volume -->
<section class="panel sales-wheel" style="left:416px;top:845px;width:300px;height:269px">
<svg viewBox="680 1381 490 439">
  <g class="ring" stroke="#fff" stroke-width="1.5">
    <path d="M873.0 1463.3A142 142 0 0 1 957.7 1452.2L947.9 1507.3A86 86 0 0 0 896.7 1514.1Z" fill="var(--peach)"/>
    <path d="M957.7 1452.2A142 142 0 0 1 1061.7 1532.0L1011.0 1555.7A86 86 0 0 0 947.9 1507.3Z" fill="var(--ink)"/>
    <path d="M1061.7 1532.0A142 142 0 0 1 1073.9 1609.3L1018.4 1602.5A86 86 0 0 0 1011.0 1555.7Z" fill="var(--navy)"/>
    <path d="M1073.9 1609.3A142 142 0 0 1 1053.4 1667.2L1005.9 1637.6A86 86 0 0 0 1018.4 1602.5Z" fill="var(--navy)"/>
    <path d="M1053.4 1667.2A142 142 0 0 1 1024.3 1700.8L988.3 1657.9A86 86 0 0 0 1005.9 1637.6Z" fill="var(--royal)"/>
    <path d="M1024.3 1700.8A142 142 0 0 1 986.2 1723.7L965.2 1671.7A86 86 0 0 0 988.3 1657.9Z" fill="var(--royal)"/>
    <path d="M986.2 1723.7A142 142 0 0 1 933 1734L933 1678A86 86 0 0 0 965.2 1671.7Z" fill="var(--royal)"/>
    <path d="M933 1734A142 142 0 0 1 877.5 1722.7L899.4 1671.2A86 86 0 0 0 933 1678Z" fill="var(--sky)"/>
    <path d="M877.5 1722.7A142 142 0 0 1 832.6 1692.4L872.2 1652.8A86 86 0 0 0 899.4 1671.2Z" fill="var(--sky)"/>
    <path d="M832.6 1692.4A142 142 0 0 1 799.6 1640.6L852.2 1621.4A86 86 0 0 0 872.2 1652.8Z" fill="var(--sky)"/>
    <path d="M799.6 1640.6A142 142 0 0 1 816.7 1510.5L862.5 1542.7A86 86 0 0 0 852.2 1621.4Z" fill="var(--orange)"/>
    <path d="M816.7 1510.5A142 142 0 0 1 873.0 1463.3L896.7 1514.1A86 86 0 0 0 862.5 1542.7Z" fill="var(--orange-soft)"/>
  </g>
  <text class="seg" x="918" y="1483">$0</text>
  <text class="seg" x="988" y="1500">COST OF SALES</text>
  <text class="seg" x="1047" y="1574">OPERATING<tspan x="1047" dy="9">EXPENSES</tspan></text>
  <text class="seg" x="1043" y="1627">FIXED<tspan x="1043" dy="9">COSTS</tspan></text>
  <text class="seg" x="1012" y="1676">TAX</text>
  <text class="seg" x="991" y="1697">INTEREST</text>
  <text class="seg" x="958" y="1713">DIVIDENDS</text>
  <text class="seg" x="906" y="1708">INV<tspan x="906" dy="9">DAYS</tspan></text>
  <text class="seg" x="870" y="1690">AP<tspan x="870" dy="9">DAYS</tspan></text>
  <text class="seg" x="845" y="1665">AR<tspan x="845" dy="9">DAYS</tspan></text>
  <text class="seg" x="820" y="1587">ADDITIONAL<tspan x="820" dy="9">DEBT</tspan></text>
  <text class="seg" x="860" y="1497">CASH<tspan x="860" dy="9">SHORTFALL</tspan></text>
  <text class="core" x="933" y="1590">NEXT $100 OF<tspan x="933" dy="21">SALES VOLUME</tspan></text>
  <g class="flags" fill="var(--orange)" stroke="var(--navy)" stroke-width="1">
    <path d="M1108 1510v16M1108 1510l12 -3v8l-12 3z"/>
    <path d="M1098 1658v16M1098 1658l12 -3v8l-12 3z"/>
    <path d="M905 1748v16M905 1748l12 -3v8l-12 3z"/>
    <path d="M742 1658v16M742 1658l-12 -3v8l12 3z"/>
    <path d="M740 1508v16M740 1508l-12 -3v8l12 3z"/>
  </g>
  <text class="out" x="933" y="1439">REVENUE $0</text>
  <text class="out" x="1086" y="1512">GROSS<tspan x="1086" dy="9">MARGIN</tspan><tspan x="1086" dy="9">$0</tspan></text>
  <text class="out" x="1080" y="1668">EBIT<tspan x="1080" dy="9">$0</tspan></text>
  <text class="out" x="942" y="1758">RETAINED<tspan x="942" dy="9">INCOME $0</tspan></text>
  <text class="out" x="770" y="1658">AFTER<tspan x="770" dy="9">WORKING</tspan><tspan x="770" dy="9">CAPITAL</tspan><tspan x="770" dy="9">$0</tspan></text>
  <text class="out" x="772" y="1507">AFTER<tspan x="772" dy="9">ADDITIONAL</tspan><tspan x="772" dy="9">FUNDING</tspan><tspan x="772" dy="9">$0</tspan></text>
</svg>
</section>

<!-- Brand -->
<div class="brand">
  <span class="brand-dot" aria-hidden="true"></span>
  <div class="brand-name">Tallowmere<br>Advisory</div>
</div>

</div>
</body>
</html>
```